Real Estate Website

I am looking for a website design for a website that will be featuring real estate listings across Australia. It will be a website for a real estate agency that operates through all states in Australia.

We like the designs of https://www.brightnest.com.au/ and https://valtoria.example/

On the brightnest website, we like the sell, buy, sold tabs but would also like lease, and agents. We also need a button somewhere for 'Join Agent Pivola' and 'Login'

On the Valtoria site it has a concierge section and we want something like that on the home page.

The contact details to show in the footer are:

Shop 2217B
Level 1 Harbourgate Shopping Centre
87 Quillon Terrace
Southport

Attached are various versions of the logo and some intro text to go on the home page.

```html
<!DOCTYPE html>
<html lang="en">
<head>
<meta charset="utf-8">
<title>Agent Pivola – Property Across Australia</title>
<link href="https://fonts.googleapis.com/css2?family=Jost:wght@400;500;600&display=swap" rel="stylesheet">
<style>
:root{
  --gold:#b8975a;
  --gold-dark:#8d6a33;
  --gold-light:#d9c49c;
  --black:#000;
  --card-dark:#1b1b1b;
  --cream:#f8f5f0;
  --ink:#1a1a1a;
  --muted:#333;
  --white:#fff;
}
*{box-sizing:border-box;margin:0;padding:0}
html,body{width:1200px;height:3857px;overflow:hidden}
body{font-family:"Jost",sans-serif;color:var(--ink);background:var(--white);position:relative}
.abs{position:absolute}
.gold{color:var(--gold)}
.btn{position:absolute;display:flex;align-items:center;justify-content:center;font-size:13px;text-transform:uppercase;letter-spacing:.2px;border-radius:4px}
.btn-gold{background:var(--gold);color:var(--white)}
.section-title{position:absolute;left:0;width:1200px;text-align:center;font-size:29px;font-weight:500;text-transform:uppercase;letter-spacing:-.3px}

/* header */
.header-band{left:0;top:0;width:1200px;height:549px;background:var(--black)}
.brand{left:148px;top:92px;color:var(--gold);font-size:14px;letter-spacing:4px;display:flex;align-items:center;gap:10px}
.brand-mark{width:12px;height:12px;border:1px solid var(--gold);border-radius:50%}
.btn-login{left:777px;top:21px;width:90px;height:34px;border:1px solid #666;color:var(--white);font-size:12px;gap:8px}
.btn-join{left:890px;top:21px;width:157px;height:34px;font-size:12px}
.main-nav{left:533px;top:78px;display:flex;gap:34px;font-size:13px;color:var(--white);font-weight:500}
.main-nav .active{color:var(--gold)}
.hero{left:111px;top:120px;width:981px;height:530px;clip-path:polygon(0 0,930px 0,981px 45px,981px 530px,20px 530px,0 510px);
  background:linear-gradient(180deg,#6c7a78 0%,#4e6140 30%,#3f6b2a 60%,#2f4e22 100%)}
.hero-shade{left:111px;top:120px;width:981px;height:530px;background:linear-gradient(180deg,rgba(0,0,0,.25),rgba(0,0,0,.05) 50%,rgba(0,0,0,.2));clip-path:polygon(0 0,930px 0,981px 45px,981px 530px,20px 530px,0 510px)}
.hero-arrow{top:318px}
.hero-title{left:153px;top:462px;color:var(--white);font-size:24px;font-weight:500;text-transform:uppercase;letter-spacing:-.3px}
.hero-tabs{left:153px;top:522px;display:flex}
.hero-tabs span{width:87px;height:34px;display:flex;align-items:center;justify-content:center;gap:6px;background:#111;color:var(--white);font-size:13px;text-transform:uppercase}
.hero-tabs .active{background:var(--gold)}
.hero-input{left:153px;top:560px;width:670px;height:44px;background:var(--white);color:#aaa;font-size:13px;padding-left:14px;display:flex;align-items:center;text-transform:uppercase}
.hero-cta{left:823px;top:560px;width:225px;height:44px;border-radius:0;font-size:14px}

/* listings */
.filters button{position:absolute;top:800px;height:35px;border:1px solid var(--gold);background:var(--white);font:13px "Jost",sans-serif;text-transform:uppercase;color:var(--ink)}
.filters .active{background:var(--gold);color:var(--white)}
.listing{position:absolute;top:885px;width:309px;height:411px;background:var(--white);box-shadow:0 0 8px rgba(0,0,0,.08);clip-path:polygon(0 0,280px 0,309px 28px,309px 411px,0 411px);text-align:center}
.listing-photo{position:absolute;left:9px;top:10px;width:292px;height:180px;clip-path:polygon(0 0,260px 0,292px 30px,292px 180px,0 180px)}
.listing-tag{position:absolute;left:20px;top:22px;font-size:13px;color:var(--white);display:flex;align-items:center;gap:6px;text-transform:uppercase}
.listing-tag i{width:11px;height:11px;display:block}
.listing h3{position:absolute;top:215px;width:100%;font-size:14px;font-weight:400;color:var(--gold-dark);text-transform:uppercase}
.listing p{position:absolute;top:251px;left:62px;right:62px;font-size:15px;line-height:34px}
.listing .price{position:absolute;top:324px;width:100%;font-size:19px;color:var(--gold-dark);font-weight:500}
.listing .specs{position:absolute;top:370px;left:0;width:100%;display:flex;justify-content:center;gap:48px;font-size:13px}
.listing .corner{position:absolute;right:0;bottom:0;width:56px;height:48px;background:var(--gold-dark);clip-path:polygon(100% 0,100% 100%,0 100%)}
.listing .corner svg{position:absolute;right:10px;bottom:8px}

/* about */
.about{left:0;top:1476px;width:1200px;height:648px;background:var(--cream)}
.about-frame{left:102px;top:1539px;width:477px;height:513px;background:var(--gold-dark);clip-path:polygon(0 20px,20px 0,420px 0,477px 50px,477px 513px,0 513px)}
.about-photo{left:112px;top:1549px;width:467px;height:503px;background:linear-gradient(135deg,#2a2e33,#55585c 55%,#8a7c6a)}
.about h2{position:absolute;left:660px;top:104px;font-size:29px;font-weight:500;text-transform:uppercase;letter-spacing:-.3px}
.about-copy{position:absolute;left:660px;top:162px;width:435px;font-size:14px;line-height:34.5px;color:var(--muted)}
.about-copy p+p{margin-top:16px}

/* concierge */
.concierge{left:0;top:2124px;width:1200px;height:686px;background:var(--black);color:var(--white)}
.concierge-sub{position:absolute;top:128px;width:1200px;text-align:center;font-size:15px}
.service{position:absolute;top:213px;width:253px;height:318px;background:var(--card-dark);border-radius:14px;clip-path:polygon(0 0,205px 0,253px 45px,253px 318px,0 318px);text-align:center}
.service svg{position:absolute;left:101px;top:20px}
.service h3{position:absolute;top:96px;width:100%;font-size:15px;font-weight:400;color:var(--gold);text-transform:uppercase}
.service p{position:absolute;top:134px;left:18px;right:18px;font-size:14.5px;line-height:34px}
.service .btn{left:76px;top:256px;width:101px;height:35px;border:1px solid var(--gold);font-size:11px;color:var(--white)}

/* areas */
.area-list{left:114px;top:2997px;display:grid;grid-template-columns:292px 200px;row-gap:20px;font-size:13px;text-transform:uppercase}
.area-list li{list-style:none;display:flex;align-items:center;gap:20px;height:26px}
.map{left:682px;top:2950px;width:410px;height:265px;background:linear-gradient(160deg,var(--gold-light),var(--gold) 60%);border-radius:6px}
.map-rule{left:640px;top:3215px;width:500px;height:1px;background:#eee}

/* join */
.join{left:0;top:3292px;width:1200px;height:208px;background:var(--gold);color:var(--white)}
.join h2{position:absolute;left:115px;top:40px;font-size:29px;font-weight:500;color:var(--ink);text-transform:uppercase;letter-spacing:-.3px}
.join p{position:absolute;left:115px;top:100px;width:520px;font-size:14.5px;line-height:35px}
.join .btn{left:829px;top:84px;width:260px;height:40px;background:var(--white);color:var(--ink)}

/* footer */
.footer{left:0;top:3500px;width:1200px;height:357px;background:var(--black);color:var(--white)}
.footer .icon-box{position:absolute;width:38px;height:38px;border:1px solid #777;border-radius:4px;display:flex;align-items:center;justify-content:center}
.footer-brand{position:absolute;left:0;width:1200px;top:160px;text-align:center;color:var(--gold);font-size:19px;letter-spacing:5px}
.footer-nav{position:absolute;top:228px;left:0;width:1200px;display:flex;justify-content:center;gap:18px;font-size:13px}
.footer-rule{position:absolute;left:150px;top:289px;width:900px;height:1px;background:#444}
.copyright{position:absolute;top:319px;width:1200px;text-align:center;font-size:12px}
</style>
</head>
<body>

<div class="abs header-band"></div>
<div class="abs brand"><span class="brand-mark"></span>AGENT PIVOLA</div>
<div class="btn btn-login">
  <svg width="10" height="11" viewBox="0 0 10 11"><circle cx="5" cy="3" r="2.5" fill="#fff"/><path d="M0 11a5 5 0 0 1 10 0z" fill="#fff"/></svg>LOGIN
</div>
<div class="btn btn-gold btn-join">JOIN AGENT PIVOLA</div>
<nav class="abs main-nav"><span class="active">HOME</span><span>BUY</span><span>SELL</span><span>LEASE</span><span>SOLD</span><span>AGENTS</span><span>CONCIERGE</span></nav>

<div class="abs hero" role="img" aria-label="Aerial view of green farmland and trees under a hazy sky"></div>
<div class="abs hero-shade"></div>
<svg class="abs hero-arrow" style="left:40px" width="16" height="24" viewBox="0 0 16 24"><path d="M11 5 4 12l7 7" stroke="#fff" stroke-width="2" fill="none"/></svg>
<svg class="abs hero-arrow" style="left:1136px" width="16" height="24" viewBox="0 0 16 24"><path d="M5 5l7 7-7 7" stroke="#fff" stroke-width="2" fill="none"/></svg>
<h1 class="abs hero-title">Your <span class="gold">central hub</span> for property across Australia</h1>
<div class="abs hero-tabs"><span class="active">Sell</span><span>Buy</span><span>Rent</span></div>
<div class="abs hero-input">Start typing to find your address</div>
<div class="btn btn-gold hero-cta">Get property estimate</div>

<h2 class="section-title" style="top:724px">Featured <span class="gold">Listings</span></h2>
<div class="filters">
  <button class="active" style="left:349px;width:83px">All</button>
  <button style="left:445px;width:122px">For Sale</button>
  <button style="left:580px;width:121px">For Lease</button>
  <button style="left:715px;width:136px">Recently Sold</button>
</div>

<article class="listing" style="left:109px">
  <div class="listing-photo" role="img" aria-label="Resort apartment with pool overlooking a marina" style="background:linear-gradient(180deg,#c9a57a,#3f6f8f 45%,#2ea3b8 80%,#a07a55)"></div>
  <div class="listing-tag"><i style="background:#f5d20a"></i>New</div>
  <h3>3 Bed Apartment in Southport</h3>
  <p>Luxurious coastal living near Harbour Quay</p>
  <div class="price">$780,000</div>
  <div class="specs"><span>🛏 3</span><span>🛁 2</span><span>🚗 1</span></div>
  <div class="corner"><svg width="10" height="12"><path d="M3 2l5 4-5 4" stroke="#fff" stroke-width="1.5" fill="none"/></svg></div>
</article>
<article class="listing" style="left:446px">
  <div class="listing-photo" role="img" aria-label="Modern two-storey townhouse under a blue sky" style="background:linear-gradient(180deg,#2f6fbf,#6b8fb0 40%,#d8d2c8 70%,#6a6a5a)"></div>
  <div class="listing-tag"><i style="background:#1db83a"></i>For Lease</div>
  <h3>Modern Townhouse in Melbourne</h3>
  <p>Close to trams, cafes, and schools</p>
  <div class="price">$650/week</div>
  <div class="specs"><span>🛏 2</span><span>🛁 2</span><span>🚗 1</span></div>
  <div class="corner"><svg width="10" height="12"><path d="M3 2l5 4-5 4" stroke="#fff" stroke-width="1.5" fill="none"/></svg></div>
</article>
<article class="listing" style="left:780px">
  <div class="listing-photo" role="img" aria-label="Couple walking toward a blue weatherboard home" style="background:linear-gradient(180deg,#5b7fa8,#45627f 45%,#5f7c45 80%,#4a6a35)"></div>
  <div class="listing-tag"><i style="background:#e02020;border-radius:50%"></i>Sold</div>
  <h3>Beachfront Home in Bondi</h3>
  <p>Sold above reserve with 12 bidders</p>
  <div class="price">$2,150,000</div>
  <div class="specs"><span>🛏 4</span><span>🛁 3</span><span>🚗 2</span></div>
  <div class="corner"><svg width="10" height="12"><path d="M3 2l5 4-5 4" stroke="#fff" stroke-width="1.5" fill="none"/></svg></div>
</article>
<div class="btn btn-gold" style="left:508px;top:1350px;width:185px;height:43px">View more listings</div>

<section class="abs about">
  <h2>About <span class="gold">Agent Pivola</span></h2>
  <div class="about-copy">
    <p>Lorem ipsum dolor sit amet, consectetur adipiscing elit, sed do eiusmod tempor incididunt ut labore et dolore magna aliqua. Ut enim ad minim veniam, quis nostrud exercitation ullamco laboris nisi ut aliquip ex ea commodo consequat.</p>
    <p>Lorem ipsum dolor sit amet, consectetur adipiscing elit, sed do eiusmod tempor incididunt ut labore et dolore magna aliqua. Ut enim ad minim veniam, quis nostrud exercitation ullamco laboris nisi ut aliquip ex ea commodo consequat.</p>
  </div>
  <div class="btn btn-gold" style="left:660px;top:483px;width:157px;height:41px">Find out more</div>
</section>
<div class="abs about-frame"></div>
<div class="abs about-photo" role="img" aria-label="Agent greeting a couple with a handshake at a front door"></div>

<section class="abs concierge">
  <h2 class="section-title" style="top:58px">Agent Pivola <span class="gold">Concierge</span></h2>
  <p class="concierge-sub">Experience real estate support beyond the sale. Agent Pivola’s concierge services are here to guide you at every step.</p>

  <div class="service" style="left:113px">
    <svg width="52" height="50" viewBox="0 0 52 50" fill="none" stroke="#b8975a" stroke-width="2"><rect x="4" y="14" width="44" height="34"/><path d="M2 16 26 2l24 14"/><rect x="20" y="32" width="12" height="16"/><rect x="10" y="22" width="6" height="6"/><rect x="36" y="22" width="6" height="6"/></svg>
    <h3>Property Styling</h3>
    <p>Maximize appeal with professional home staging and interior advice.</p>
    <div class="btn">Learn more</div>
  </div>
  <div class="service" style="left:409px">
    <svg width="52" height="50" viewBox="0 0 52 50" fill="none" stroke="#fff" stroke-width="2"><path d="M6 22 26 6l20 16v26H6z"/><rect x="20" y="32" width="12" height="16"/><circle cx="38" cy="14" r="6" stroke="#b8975a"/></svg>
    <h3>Mortgage Advice</h3>
    <p>Get connected with leading brokers to find the best home loan deals.</p>
    <div class="btn">Learn more</div>
  </div>
  <div class="service" style="left:703px">
    <svg width="52" height="50" viewBox="0 0 52 50" fill="none" stroke="#fff" stroke-width="2"><rect x="4" y="4" width="30" height="42"/><path d="M10 14h18M10 22h18M10 30h18M10 38h12"/><circle cx="42" cy="16" r="8" stroke="#b8975a"/></svg>
    <h3>Legal Support</h3>
    <p>Access trusted conveyancers and property solicitors to protect your purchase.</p>
    <div class="btn">Learn more</div>
  </div>
  <div class="service" style="left:998px">
    <svg width="52" height="50" viewBox="0 0 52 50" fill="none" stroke="#fff" stroke-width="2"><rect x="6" y="10" width="20" height="26"/><rect x="28" y="16" width="18" height="20"/><path d="M4 36h44v6H4z" stroke="#b8975a"/><circle cx="14" cy="44" r="3"/><circle cx="38" cy="44" r="3"/></svg>
    <h3>Moving Services</h3>
    <p>Partnered moving teams help you relocate with ease, anywhere in Australia.</p>
    <div class="btn">Learn more</div>
  </div>

  <div class="btn btn-gold" style="left:471px;top:577px;width:259px;height:41px">Learn more about concierge</div>
</section>

<h2 class="section-title" style="top:2885px">Areas we <span class="gold">serve</span></h2>
<ul class="abs area-list">
  <li><svg width="11" height="15" viewBox="0 0 11 15"><path d="M5.5 0A5.5 5.5 0 0 0 0 5.5C0 9.5 5.5 15 5.5 15S11 9.5 11 5.5A5.5 5.5 0 0 0 5.5 0z" fill="#b8975a"/><circle cx="5.5" cy="5.5" r="2" fill="#fff"/></svg>New South Wales</li>
  <li><svg width="11" height="15" viewBox="0 0 11 15"><path d="M5.5 0A5.5 5.5 0 0 0 0 5.5C0 9.5 5.5 15 5.5 15S11 9.5 11 5.5A5.5 5.5 0 0 0 5.5 0z" fill="#b8975a"/><circle cx="5.5" cy="5.5" r="2" fill="#fff"/></svg>South Australia</li>
  <li><svg width="11" height="15" viewBox="0 0 11 15"><path d="M5.5 0A5.5 5.5 0 0 0 0 5.5C0 9.5 5.5 15 5.5 15S11 9.5 11 5.5A5.5 5.5 0 0 0 5.5 0z" fill="#b8975a"/><circle cx="5.5" cy="5.5" r="2" fill="#fff"/></svg>Victoria</li>
  <li><svg width="11" height="15" viewBox="0 0 11 15"><path d="M5.5 0A5.5 5.5 0 0 0 0 5.5C0 9.5 5.5 15 5.5 15S11 9.5 11 5.5A5.5 5.5 0 0 0 5.5 0z" fill="#b8975a"/><circle cx="5.5" cy="5.5" r="2" fill="#fff"/></svg>Tasmania</li>
  <li><svg width="11" height="15" viewBox="0 0 11 15"><path d="M5.5 0A5.5 5.5 0 0 0 0 5.5C0 9.5 5.5 15 5.5 15S11 9.5 11 5.5A5.5 5.5 0 0 0 5.5 0z" fill="#b8975a"/><circle cx="5.5" cy="5.5" r="2" fill="#fff"/></svg>Queensland</li>
  <li><svg width="11" height="15" viewBox="0 0 11 15"><path d="M5.5 0A5.5 5.5 0 0 0 0 5.5C0 9.5 5.5 15 5.5 15S11 9.5 11 5.5A5.5 5.5 0 0 0 5.5 0z" fill="#b8975a"/><circle cx="5.5" cy="5.5" r="2" fill="#fff"/></svg>ACT</li>
  <li><svg width="11" height="15" viewBox="0 0 11 15"><path d="M5.5 0A5.5 5.5 0 0 0 0 5.5C0 9.5 5.5 15 5.5 15S11 9.5 11 5.5A5.5 5.5 0 0 0 5.5 0z" fill="#b8975a"/><circle cx="5.5" cy="5.5" r="2" fill="#fff"/></svg>Western Australia</li>
  <li><svg width="11" height="15" viewBox="0 0 11 15"><path d="M5.5 0A5.5 5.5 0 0 0 0 5.5C0 9.5 5.5 15 5.5 15S11 9.5 11 5.5A5.5 5.5 0 0 0 5.5 0z" fill="#b8975a"/><circle cx="5.5" cy="5.5" r="2" fill="#fff"/></svg>Northern Territory</li>
</ul>
<div class="abs map" role="img" aria-label="Map of Australia in gold with location pins marking each state and territory"></div>
<div class="abs map-rule"></div>

<section class="abs join">
  <h2>Join Agent Pivola</h2>
  <p>Lorem ipsum dolor sit amet, consectetur adipiscing elit, sed do eiusmod tempor incididunt ut labore et dolore magna aliqua.</p>
  <div class="btn">Become a partner agent</div>
</section>

<footer class="abs footer">
  <div class="icon-box" style="left:271px;top:100px"><svg width="16" height="16" viewBox="0 0 24 24"><path d="M6.6 10.8a15 15 0 0 0 6.6 6.6l2.2-2.2a1 1 0 0 1 1-.25 11.4 11.4 0 0 0 3.6.57 1 1 0 0 1 1 1V20a1 1 0 0 1-1 1A17 17 0 0 1 3 4a1 1 0 0 1 1-1h3.5a1 1 0 0 1 1 1c0 1.25.2 2.45.57 3.57a1 1 0 0 1-.25 1z" fill="#fff"/></svg></div>
  <div class="abs" style="left:333px;top:109px;font-size:14px">+61 7 5550 0199</div>
  <div class="footer-brand">AGENT PIVOLA</div>
  <div class="icon-box" style="left:751px;top:100px"><svg width="14" height="18" viewBox="0 0 11 15"><path d="M5.5 0A5.5 5.5 0 0 0 0 5.5C0 9.5 5.5 15 5.5 15S11 9.5 11 5.5A5.5 5.5 0 0 0 5.5 0z" fill="#fff"/><circle cx="5.5" cy="5.5" r="2" fill="#000"/></svg></div>
  <div class="abs" style="left:826px;top:76px;font-size:13px;line-height:31px;text-transform:uppercase">Shop 2217B Level 1 Harbourgate<br>Shopping Centre 87 Quillon Terrace<br>Southport</div>
  <nav class="footer-nav"><span>HOME</span><span>|</span><span>BUY</span><span>|</span><span>SELL</span><span>|</span><span>LEASE</span><span>|</span><span>SOLD</span><span>|</span><span>AGENTS</span><span>|</span><span>CONCIERGE</span><span>|</span><span>CONTACT US</span></nav>
  <div class="footer-rule"></div>
  <div class="copyright">©2025 COPYRIGHTS | ALL RIGHTS RESERVED</div>
</footer>

</body>
</html>
```